New business card design

I need original, modern, business looking but dzen (minimalistic) looking design.
Also refer to websit travenko.ru

Text is

Веденин Олег, PMP
Партнер

Моб. +7 (915) 604 7189
info@travenko.ru
Москва, Россия, 127318, ул. Берёзовая 27/2
=====================

Vedenin Oleg, PMP
Partner

Mob. +7 (915) 604 7189
info@travenko.ru
Moscow, Russia,127318, Beryozovaya 27/2

```html
<!DOCTYPE html>
<html lang="ru">
<head>
<meta charset="utf-8">
<title>Travenko — business cards</title>
<link rel="stylesheet" href="https://fonts.googleapis.com/css2?family=Open+Sans:wght@300;400;700&display=swap">
<style>
  :root {
    --bg: #e9e6e1;
    --card: #fbfbfb;
    --card-shade: #eeeeee;
    --decor: #f0f0f0;
    --accent: #2bb3d8;
    --ink: #2b2b2b;
    --muted: #4a4a4a;
    --icon: #2a9fcf;
  }
  html, body {
    margin: 0;
    width: 1200px;
    height: 903px;
    overflow: hidden;
    background: var(--bg);
    font-family: "Open Sans", Arial, sans-serif;
  }
  .stage {
    position: relative;
    width: 1200px;
    height: 903px;
  }
  .card {
    position: absolute;
    top: 296px;
    width: 540px;
    height: 310px;
    border-radius: 22px;
    background: linear-gradient(100deg, var(--card) 55%, var(--card-shade) 100%);
    box-shadow: 0 3px 0 #dcdcdc, 0 6px 0 #e6e6e6, 0 14px 30px rgba(0,0,0,0.18);
    overflow: hidden;
  }
  .card--ru { left: 40px; }
  .card--en { left: 620px; }

  .card__decor {
    position: absolute;
    right: -40px;
    top: 30px;
    width: 220px;
    height: 220px;
    background: var(--decor);
    transform: rotate(45deg);
    border-radius: 14px;
  }

  .brand {
    position: absolute;
    left: 42px;
    top: 62px;
    display: flex;
    align-items: center;
    gap: 18px;
  }
  .brand__mark {
    width: 54px;
    height: 54px;
    background: var(--accent);
    border-radius: 6px;
  }
  .brand__name {
    font-weight: 300;
    font-size: 58px;
    line-height: 1;
    color: var(--accent);
    letter-spacing: -1px;
  }

  .person {
    position: absolute;
    left: 42px;
    top: 160px;
  }
  .person__name {
    margin: 0;
    font-weight: 700;
    font-size: 17px;
    text-transform: uppercase;
    color: var(--accent);
  }
  .person__role {
    margin: 2px 0 0;
    font-size: 15px;
    color: var(--ink);
  }

  .contacts {
    position: absolute;
    left: 42px;
    top: 222px;
    margin: 0;
    padding: 0;
    list-style: none;
    font-size: 13px;
    line-height: 19px;
    color: var(--muted);
  }
  .contacts li {
    display: flex;
    align-items: center;
    gap: 9px;
  }
  .contacts svg { width: 11px; height: 11px; fill: var(--icon); }

  .address {
    position: absolute;
    left: 300px;
    top: 222px;
    margin: 0;
    font-style: normal;
    font-size: 13px;
    line-height: 19px;
    color: var(--muted);
  }
</style>
</head>
<body>
<main class="stage">

  <article class="card card--ru" lang="ru">
    <div class="card__decor"></div>
    <div class="brand">
      <div class="brand__mark"></div>
      <span class="brand__name">Travenko</span>
    </div>
    <div class="person">
      <h2 class="person__name">Веденин Олег, PMP</h2>
      <p class="person__role">Партнер</p>
    </div>
    <ul class="contacts">
      <li><svg viewBox="0 0 12 12"><path d="M2 1l2 0 1 3-1.5 1a7 7 0 0 0 3.5 3.5L8 7l3 1v2c0 1-1 1-1 1A9 9 0 0 1 1 2s0-1 1-1z"/></svg>+7 (915) 604 7189</li>
      <li><svg viewBox="0 0 12 12"><path d="M0 2h12v8H0z M0 2l6 4 6-4"/></svg>info@travenko.ru</li>
      <li><svg viewBox="0 0 12 12"><circle cx="6" cy="6" r="6"/></svg>www.travenko.ru</li>
    </ul>
    <address class="address">Москва, Россия,<br>127318, ул. Берёзовая 27/2</address>
  </article>

  <article class="card card--en" lang="en">
    <div class="card__decor"></div>
    <div class="brand">
      <div class="brand__mark"></div>
      <span class="brand__name">Travenko</span>
    </div>
    <div class="person">
      <h2 class="person__name">Vedenin Oleg, PMP</h2>
      <p class="person__role">Partner</p>
    </div>
    <ul class="contacts">
      <li><svg viewBox="0 0 12 12"><path d="M2 1l2 0 1 3-1.5 1a7 7 0 0 0 3.5 3.5L8 7l3 1v2c0 1-1 1-1 1A9 9 0 0 1 1 2s0-1 1-1z"/></svg>+7 (915) 604 7189</li>
      <li><svg viewBox="0 0 12 12"><path d="M0 2h12v8H0z M0 2l6 4 6-4"/></svg>info@travenko.ru</li>
      <li><svg viewBox="0 0 12 12"><circle cx="6" cy="6" r="6"/></svg>www.travenko.ru</li>
    </ul>
    <address class="address">Moscow, Russia,<br>127318, Beryozovaya 27/2</address>
  </article>

</main>
</body>
</html>
```